Home Remodeling company needs a business card design

we need a business card design for home remodeling company in hamilton county, indiana USA. we offers a wide range of construction services including whole house renovations, Design and Build Basements and Kitchen and Bathroom Remodeling . we would like to see designs for both site of business card that use the same color of the company logo and also including all information below :
1- Karim Feltous CEO / General Contractor
2- all company contacts Telephone numbers ( 1-888-DULOM-47 ) ( 317-555-0193) email address ( info@dulomhome.com) website ( www.dulomhome.com ) and social media logos (Facebook- twitter- google plus )
3- company logo
4- licensed . insured . bonded

```html
<!DOCTYPE html>
<html lang="en">
<head>
<meta charset="utf-8">
<title>Dulom Home Remodeling – Business Card</title>
<link href="https://fonts.googleapis.com/css2?family=Roboto:wght@400&display=swap" rel="stylesheet">
<style>
  :root {
    --bg: #ecebe8;
    --charcoal: #3a3a3c;
    --charcoal-dark: #2b2b2d;
    --band: #343436;
    --red: #c02a3a;
    --white: #ffffff;
    --grey-text: #6d6d70;
    --card-shadow: 0 10px 28px rgba(0,0,0,0.22);
  }
  * { box-sizing: border-box; margin: 0; padding: 0; }
  html, body { width: 1200px; height: 902px; overflow: hidden; background: var(--bg); }
  .canvas {
    width: 1200px; height: 902px;
    display: flex; flex-direction: column; align-items: center; justify-content: center; gap: 60px;
  }
  .card {
    width: 630px; height: 360px; position: relative; overflow: hidden;
    box-shadow: var(--card-shadow);
    font-family: "Roboto", sans-serif; font-weight: 400;
  }

  /* Brand name set as plain text */
  .brand { display: flex; flex-direction: column; align-items: flex-start; }
  .brand__row { display: flex; align-items: center; gap: 14px; }
  .brand__square { width: 16px; height: 16px; flex: none; }
  .brand__name { line-height: 1; letter-spacing: 2px; }
  .brand__tagline { text-transform: uppercase; letter-spacing: 6px; margin-top: 8px; padding-left: 30px; }

  /* Back side */
  .card--back {
    background: linear-gradient(160deg, var(--charcoal) 0%, var(--charcoal-dark) 100%);
    display: flex; align-items: center; justify-content: center;
  }
  .card--back .brand__square { background: var(--white); }
  .card--back .brand__name { color: var(--white); font-size: 88px; }
  .card--back .brand__tagline { color: var(--white); font-size: 20px; }

  /* Front side */
  .card--front { background: var(--white); }
  .front__top {
    position: absolute; left: 0; top: 0; width: 100%; height: 168px;
    display: flex; align-items: center; justify-content: center;
  }
  .card--front .brand__square { background: var(--red); }
  .card--front .brand__name { color: var(--charcoal); font-size: 62px; }
  .card--front .brand__tagline { color: var(--grey-text); font-size: 15px; margin-top: 6px; }
  .brand__claims { color: var(--grey-text); font-size: 18px; padding-left: 30px; margin-top: 4px; }
  .front__band { position: absolute; left: 0; top: 168px; width: 100%; height: 14px; background: var(--band); }
  .front__bottom {
    position: absolute; left: 0; top: 182px; width: 100%; height: 178px;
    background: var(--red); color: var(--white);
    display: flex; align-items: flex-end; justify-content: space-between;
    padding: 0 30px 26px 34px;
  }
  .person__name { font-size: 30px; line-height: 1.1; }
  .person__role { font-size: 20px; }
  .contacts-block {
    align-self: center; border-left: 2px solid var(--white); padding-left: 16px;
  }
  .contacts { list-style: none; font-size: 17px; }
  .contacts li { display: flex; align-items: center; gap: 12px; height: 28px; }
  .contacts svg { width: 18px; height: 18px; flex: none; }
  .social { display: flex; gap: 10px; margin-top: 8px; }
  .social__badge { width: 20px; height: 20px; border-radius: 50%; background: var(--white); }
</style>
</head>
<body>
<main class="canvas">

  <section class="card card--back" aria-label="Business card back">
    <div class="brand">
      <div class="brand__row">
        <span class="brand__square"></span>
        <span class="brand__name">DULOM</span>
      </div>
      <span class="brand__tagline">Home Remodeling</span>
    </div>
  </section>

  <section class="card card--front" aria-label="Business card front">
    <div class="front__top">
      <div class="brand">
        <div class="brand__row">
          <span class="brand__square"></span>
          <span class="brand__name">DULOM</span>
        </div>
        <span class="brand__tagline">Home Remodeling</span>
        <span class="brand__claims">LICENSED . INSURED . BONDED</span>
      </div>
    </div>
    <div class="front__band"></div>
    <div class="front__bottom">
      <div class="person">
        <p class="person__name">Karim Feltous</p>
        <p class="person__role">CEO / General Contractor</p>
      </div>
      <div class="contacts-block">
        <ul class="contacts">
          <li>
            <svg viewBox="0 0 20 20"><rect width="20" height="20" rx="2" fill="#fff"/><path d="M5 7c0-1.5 2-2 5-2s5 .5 5 2l-1.5 1.5-2-1v-1h-3v1l-2 1z M6 10h8v4H6z" fill="#c02a3a"/></svg>
            <span>1-888-DULOM-47</span>
          </li>
          <li>
            <svg viewBox="0 0 20 20"><rect width="20" height="20" rx="2" fill="#fff"/><rect x="7" y="4" width="6" height="12" rx="1" fill="#c02a3a"/><rect x="8" y="5.5" width="4" height="7" fill="#fff"/></svg>
            <span>317-555-0193</span>
          </li>
          <li>
            <svg viewBox="0 0 20 20"><rect width="20" height="20" rx="2" fill="#fff"/><rect x="4" y="6" width="12" height="8" fill="#c02a3a"/><path d="M4 6l6 5 6-5" fill="none" stroke="#fff" stroke-width="1.2"/></svg>
            <span>info@dulomhome.com</span>
          </li>
          <li>
            <svg viewBox="0 0 20 20"><rect width="20" height="20" rx="2" fill="#fff"/><circle cx="10" cy="10" r="6" fill="none" stroke="#c02a3a" stroke-width="1.5"/><path d="M4 10h12M10 4c-3 3-3 9 0 12M10 4c3 3 3 9 0 12" fill="none" stroke="#c02a3a" stroke-width="1.1"/></svg>
            <span>www.dulomhome.com</span>
          </li>
        </ul>
        <div class="social" aria-label="Social media">
          <span class="social__badge" role="img" aria-label="Social network badge"></span>
          <span class="social__badge" role="img" aria-label="Social network badge"></span>
          <span class="social__badge" role="img" aria-label="Social network badge"></span>
        </div>
      </div>
    </div>
  </section>

</main>
</body>
</html>
```